Maris Dovey Studio Business Cards

Hi - using the information and logo provided I require a two sided business card designed with the following information. The business card is a 'mini card' 3.5" x 1.25".

Front of card should be the logo attached but inverted (so the background is the peach colour and the logo white).

Back should have these details. If we can't fit the Pictogrum and Friendwall part can we just put the little logos.

Tessa Varnold

Art and Design Consultant
Dealer - Curator - Events - Styling - Creative Sourcing

P: 0438 217 604
E: tessa@marisdoveystudio.example
W: www.marisdoveystudio.example
I (pictogram image please): marisdoveystudio F (Friendwall image please): MarisDoveyAdviser

Target Market(s)

Galleries, artists, art buyers, interior design clients, event managers, creative types

Industry/Entity Type

Business

```html
<!DOCTYPE html>
<html lang="en">
<head>
<meta charset="utf-8">
<title>Maris Dovey Studio — Mini Business Card</title>
<link rel="stylesheet" href="https://fonts.googleapis.com/css2?family=Tinos:wght@400&display=swap">
<style>
  :root {
    --peach: #f0b596;
    --ink: #151313;
    --text-dark: #1c1b1b;
    --paper: #ffffff;
    --rule: #5a5a5a;
    --rule-soft: #4a4646;
    --backdrop: #ebe8e5;
  }
  * { box-sizing: border-box; margin: 0; padding: 0; }
  html, body {
    width: 1200px; height: 960px; overflow: hidden;
    background: var(--backdrop);
    font-family: "Tinos", "Times New Roman", serif;
  }
  .canvas { position: relative; width: 1200px; height: 960px; }

  .card { position: absolute; width: 780px; height: 279px; }

  /* Front */
  .card-front { left: 58px; top: 67px; background: var(--ink); }
  .brand-panel {
    position: absolute; left: 37px; top: 0; width: 283px; height: 191px;
    background: var(--paper);
    border-radius: 0 0 16px 16px;
    display: flex; align-items: center; justify-content: center;
  }
  .brand-name {
    color: var(--peach); font-size: 30px; line-height: 1.15;
    text-align: center; letter-spacing: 1px;
  }
  .accent-bar {
    position: absolute; left: 341px; top: 27px; width: 439px; height: 5px;
    background: var(--peach);
  }
  .holder-name {
    position: absolute; left: 341px; top: 62px;
    color: var(--peach); font-size: 34px; letter-spacing: 0.5px;
  }
  .holder-role {
    position: absolute; left: 341px; top: 105px;
    color: var(--peach); font-size: 19px;
  }
  .services-rule {
    position: absolute; left: 26px; width: 724px; height: 1px;
    background: var(--rule-soft);
  }
  .services-rule.top { top: 217px; }
  .services-rule.bottom { top: 258px; }
  .services {
    position: absolute; left: 26px; width: 724px; top: 225px;
    text-align: center; color: var(--peach); font-size: 22px;
  }

  /* Back */
  .card-back { left: 383px; top: 479px; background: var(--paper); }
  .back-rule {
    position: absolute; left: 28px; width: 721px; height: 1px;
    background: var(--rule);
  }
  .back-rule.r1 { top: 23px; }
  .back-rule.r2 { top: 206px; }
  .back-rule.r3 { top: 254px; }
  .back-brand {
    position: absolute; left: 36px; top: 42px; width: 160px; height: 146px;
    display: flex; flex-direction: column; align-items: center; justify-content: center;
    gap: 10px;
  }
  .back-brand .dot {
    width: 26px; height: 26px; border-radius: 50%; background: var(--peach);
  }
  .back-brand .brand-name { font-size: 24px; }
  .contact-line {
    position: absolute; left: 251px; color: var(--text-dark); font-size: 25px;
  }
  .contact-line.phone { top: 62px; }
  .contact-line.email { top: 107px; }
  .contact-line.web { top: 149px; }
  .social {
    position: absolute; top: 215px; display: flex; align-items: center; gap: 12px;
    color: var(--text-dark); font-size: 22px;
  }
  .social .marker {
    width: 32px; height: 32px; background: #333; border-radius: 3px;
  }
  .social.friendwall { left: 43px; }
  .social.pictogram { left: 433px; }
</style>
</head>
<body>
<main class="canvas">

  <section class="card card-front" aria-label="Card front">
    <div class="brand-panel">
      <span class="brand-name">Maris Dovey<br>Studio</span>
    </div>
    <div class="accent-bar"></div>
    <h1 class="holder-name">Tessa Varnold</h1>
    <p class="holder-role">(Art and Design Consultant)</p>
    <div class="services-rule top"></div>
    <p class="services">Dealer | Curator | Events | Styling | Creative Sourcing</p>
    <div class="services-rule bottom"></div>
  </section>

  <section class="card card-back" aria-label="Card back">
    <div class="back-rule r1"></div>
    <div class="back-brand">
      <span class="dot"></span>
      <span class="brand-name">Maris Dovey<br>Studio</span>
    </div>
    <p class="contact-line phone">T: 0438 217 604</p>
    <p class="contact-line email">E: tessa@marisdoveystudio.example</p>
    <p class="contact-line web">W: www.marisdoveystudio.example</p>
    <div class="back-rule r2"></div>
    <div class="social friendwall" aria-label="Friendwall">
      <span class="marker"></span><span>marisdoveystudio</span>
    </div>
    <div class="social pictogram" aria-label="Pictogrum">
      <span class="marker"></span><span>MarisDoveyAdviser</span>
    </div>
    <div class="back-rule r3"></div>
  </section>

</main>
</body>
</html>
```